Remodel Flyer for realtors

"R" Anchored Builders

4"x 9" rack card front and back

www.BrevinHomeworks.com

555-318-4762

Let us fix what your home inspector finds!

Send us your inspection summary.

We are a licensed and Insured contractor.
CRC4870213

Serving
Marion County and The Hollows

This flyer will sit in realtor offices for realtors to give to there buyers and sellers.

Target Market(s)

Realtors

Industry/Entity Type

Construction

Colors

Designer to choose colors to be used in the design.

```html
<!DOCTYPE html>
<html lang="en">
<head>
<meta charset="utf-8">
<title>R Anchored Builders – Rack Card</title>
<link href="https://fonts.googleapis.com/css2?family=Roboto+Condensed:wght@400;700&family=Montserrat:wght@400;500;600&display=swap" rel="stylesheet">
<style>
:root{
  --bg:#efefef;
  --orange:#f0900a;
  --orange-text:#f29a12;
  --dark:#3c3c3c;
  --darker:#2c2c2c;
  --ink:#3a3a3a;
  --white:#ffffff;
}
*{box-sizing:border-box;margin:0;padding:0}
html,body{width:1200px;height:1200px;overflow:hidden;background:var(--bg)}
body{position:relative;font-family:"Montserrat",sans-serif;color:var(--ink)}
.card{position:absolute;top:117px;width:429px;height:966px;background:var(--white);overflow:hidden;border:1px solid #d8d8d8}
.card--front{left:144px}
.card--back{left:628px}
.abs{position:absolute}

/* front */
.front-top{left:0;top:0;width:100%;height:451px;background:linear-gradient(#f6f6f6,#e9e9e9)}
.brand-name{left:0;width:100%;top:112px;text-align:center;font-family:"Montserrat",sans-serif;font-weight:600;font-size:22px;line-height:28px;color:var(--dark)}
.hero-photo{left:0;top:155px;width:100%;height:296px;background:linear-gradient(160deg,#ece8e2 0%,#d8c3a5 45%,#b9804c 100%)}
.front-panel{left:0;top:451px;width:100%;height:370px;background:var(--dark)}
.service{top:418px;width:92px;margin-left:-46px;text-align:center}
.service-icon{width:58px;height:58px;border-radius:50%;background:var(--orange);margin:0 auto;display:flex;align-items:center;justify-content:center;box-shadow:0 2px 4px rgba(0,0,0,.35)}
.service-icon span{width:46px;height:46px;border-radius:50%;background:#6a6a6a;display:flex;align-items:center;justify-content:center}
.service-label{font-family:"Roboto Condensed",sans-serif;color:var(--white);font-size:16px;margin-top:6px;white-space:nowrap}
.headline{left:0;width:100%;top:532px;text-align:center;font-family:"Roboto Condensed",sans-serif;font-weight:700;font-size:39px;line-height:48px;color:var(--white)}
.headline em{font-style:normal;color:var(--orange-text)}
.divider{left:30px;top:648px;width:368px;height:1px;background:#cfcfcf}
.divider-thick{left:152px;top:647px;width:124px;height:4px;background:var(--white)}
.front-copy{left:32px;width:365px;text-align:center;font-size:13.2px;line-height:17.6px;color:var(--white);font-weight:600}
.front-copy b{font-weight:600;color:var(--orange-text)}
.front-rule{left:30px;top:823px;width:368px;height:2px;background:var(--orange)}
.phone-big{left:0;width:100%;top:838px;text-align:center;font-family:"Roboto Condensed",sans-serif;font-weight:700;font-size:39px;color:var(--dark);display:flex;justify-content:center;align-items:center;gap:10px}

/* shared bottom */
.bottom-band{left:0;top:919px;width:100%;height:47px;background:var(--orange)}
.url-pill{left:42px;top:897px;width:344px;height:36px;border-radius:18px;background:var(--dark);border:2px solid #e9e9e9;color:var(--white);font-size:16px;letter-spacing:3.4px;display:flex;align-items:center;justify-content:center}
.url-pill b{font-weight:600;color:var(--orange-text)}

/* back */
.photo-bedroom{left:30px;top:30px;width:368px;height:231px;background:linear-gradient(180deg,#e8e2d4 0%,#d9cdb4 55%,#b39a78 100%);border:1px solid #999}
.photo-kitchen{left:30px;top:279px;width:175px;height:139px;background:linear-gradient(180deg,#e6e6e6 0%,#4a4a4a 55%,#2b2b2b 100%);border:1px solid #999}
.photo-living{left:223px;top:279px;width:175px;height:139px;background:linear-gradient(180deg,#e4d2a8 0%,#d9c7a8 55%,#c9782e 100%);border:1px solid #999}
.back-panel{left:0;top:456px;width:100%;height:310px;background:var(--dark)}
.pill-rule{left:30px;top:459px;width:368px;height:2px;background:var(--white)}
.section-pill{left:108px;top:444px;width:210px;height:36px;border-radius:18px;background:var(--darker);color:var(--orange-text);font-size:26px;font-weight:600;text-align:center;line-height:36px}
.section-head{left:0;width:100%;text-align:center;color:var(--orange-text);font-size:17px;font-weight:500}
.section-body{left:30px;width:368px;color:var(--white);font-size:11.4px;line-height:14.4px;text-align:justify;text-align-last:center}
.section-body--promise{left:26px;width:376px;font-size:11px}
.license-bar{left:30px;top:769px;width:368px;height:26px;background:var(--orange);color:var(--white);font-size:12.5px;font-weight:600;display:flex;align-items:center;padding-left:10px;white-space:nowrap}
.license-bar span{color:#2c2c2c;font-weight:500;margin-left:2px}
.contact{left:0;width:100%;text-align:center;font-size:13.6px;line-height:18px;color:var(--ink)}
.call{left:0;width:100%;top:863px;text-align:center;font-family:"Roboto Condensed",sans-serif;font-weight:700;font-size:20px;color:var(--dark)}
</style>
</head>
<body>

<section class="card card--front">
  <div class="abs front-top"></div>
  <div class="abs hero-photo" role="img" aria-label="Bright open-plan living room with beige sectional sofas, wood floor and a spiral staircase"></div>
  <div class="abs brand-name">"R" Anchored Builders</div>

  <div class="abs front-panel"></div>

  <div class="abs service" style="left:60px">
    <div class="service-icon"><span>
      <svg width="26" height="22" viewBox="0 0 26 22" fill="none" stroke="#fff" stroke-width="1.6"><rect x="2" y="9" width="22" height="11"/><line x1="13" y1="9" x2="13" y2="20"/><circle cx="7" cy="5" r="2"/><rect x="17" y="2" width="4" height="5"/></svg>
    </span></div>
    <div class="service-label">Kitchens</div>
  </div>
  <div class="abs service" style="left:154px">
    <div class="service-icon"><span>
      <svg width="26" height="22" viewBox="0 0 26 22" fill="none" stroke="#fff" stroke-width="1.6"><path d="M2 11h22v3a5 5 0 0 1-5 5H7a5 5 0 0 1-5-5z"/><path d="M20 11V4a2 2 0 0 1 4 0"/><line x1="6" y1="19" x2="5" y2="21"/><line x1="20" y1="19" x2="21" y2="21"/></svg>
    </span></div>
    <div class="service-label">Bathrooms</div>
  </div>
  <div class="abs service" style="left:252px">
    <div class="service-icon"><span>
      <svg width="22" height="24" viewBox="0 0 22 24" fill="none" stroke="#fff" stroke-width="1.6"><rect x="3" y="2" width="14" height="19"/><line x1="6" y1="7" x2="14" y2="7"/><line x1="6" y1="11" x2="14" y2="11"/><line x1="6" y1="15" x2="11" y2="15"/><circle cx="17" cy="18" r="3.5"/></svg>
    </span></div>
    <div class="service-label">Additions</div>
  </div>
  <div class="abs service" style="left:356px">
    <div class="service-icon"><span>
      <svg width="24" height="22" viewBox="0 0 24 22" fill="none" stroke="#fff" stroke-width="1.6"><path d="M2 10L12 2l10 8"/><rect x="5" y="9" width="14" height="11"/><rect x="10" y="14" width="4" height="6"/></svg>
    </span></div>
    <div class="service-label">Whole Homes</div>
  </div>

  <h1 class="abs headline">Let us fix what your<br><em>home inspector finds!</em></h1>
  <div class="abs divider"></div>
  <div class="abs divider-thick"></div>

  <p class="abs front-copy" style="top:795px;top:678px">Whether it's getting your home remodeled or fixing damage that's been done to your home, we're here to help you every step of the way.</p>
  <p class="abs front-copy" style="top:748px"><b>"R" Anchored Builders</b> has been around since <b>1976</b>, so we really mean it when we say we're here to help you.</p>

  <div class="abs front-rule"></div>
  <div class="abs phone-big">
    <svg width="30" height="30" viewBox="0 0 24 24" fill="var(--dark)"><path d="M6.6 10.8a15.1 15.1 0 0 0 6.6 6.6l2.2-2.2a1 1 0 0 1 1-.25 11.4 11.4 0 0 0 3.6.6 1 1 0 0 1 1 1V20a1 1 0 0 1-1 1A17 17 0 0 1 3 4a1 1 0 0 1 1-1h3.5a1 1 0 0 1 1 1c0 1.25.2 2.45.6 3.6a1 1 0 0 1-.25 1z"/></svg>
    <span>555-318-4762</span>
  </div>

  <div class="abs bottom-band"></div>
  <div class="abs url-pill">www.<b>brevinhomeworks</b>.com</div>
</section>

<section class="card card--back">
  <div class="abs photo-bedroom" role="img" aria-label="Bright master bedroom with a made bed, ceiling lamp and large windows"></div>
  <div class="abs photo-kitchen" role="img" aria-label="Modern kitchen with dark cabinets, stainless ovens and a bar-stool island"></div>
  <div class="abs photo-living" role="img" aria-label="Warm living room with fireplace, white sofas and hardwood floor"></div>

  <div class="abs back-panel"></div>
  <div class="abs pill-rule"></div>
  <h2 class="abs section-pill">Our Services</h2>

  <h3 class="abs section-head" style="top:495px">Residential or Commercial</h3>
  <p class="abs section-body" style="top:522px">We've got all your needs covered: from residential remodels, to commercial damage repairs and everything in between. Don't hesitate to ask us a question or inquire as to why a certain process has to take place. All of our staff are friendly and knowledgeable because we know what it's like to be in your shoes. We want you to know just how special you and your project are to us, so we do our very best to ensure that you and your needs always come first. We even have a complimentary estimate where we'll come out to you!</p>

  <h3 class="abs section-head" style="top:672px">Our Promise</h3>
  <p class="abs section-body section-body--promise" style="top:702px">Our work is good. We promise. And behind that promise, we want you to know that we back our work with a satisfaction guarantee. We won't stop working until you like what we've done.</p>

  <div class="abs license-bar">We are a licensed and Insured contractor.<span>CRC4870213</span></div>

  <p class="abs contact" style="top:803px">
    <svg width="11" height="14" viewBox="0 0 12 16" fill="none" stroke="var(--orange)" stroke-width="1.6"><path d="M6 15s5-5.5 5-9A5 5 0 0 0 1 6c0 3.5 5 9 5 9z"/><circle cx="6" cy="6" r="1.8"/></svg>
    418 Linden Ridge Rd, Marlow, Florida 34999,<br>United States
  </p>
  <p class="abs contact" style="top:841px">
    <svg width="16" height="11" viewBox="0 0 16 11" fill="none" stroke="var(--orange)" stroke-width="1.3"><rect x="4" y="1" width="11" height="9"/><path d="M4 1l5.5 5L15 1"/><line x1="0" y1="4" x2="3" y2="4"/><line x1="1" y1="7" x2="3" y2="7"/></svg>
    dana@brevinhomeworks.com
  </p>
  <p class="abs call">Call us today!
    <svg width="15" height="15" viewBox="0 0 24 24" fill="var(--dark)"><path d="M6.6 10.8a15.1 15.1 0 0 0 6.6 6.6l2.2-2.2a1 1 0 0 1 1-.25 11.4 11.4 0 0 0 3.6.6 1 1 0 0 1 1 1V20a1 1 0 0 1-1 1A17 17 0 0 1 3 4a1 1 0 0 1 1-1h3.5a1 1 0 0 1 1 1c0 1.25.2 2.45.6 3.6a1 1 0 0 1-.25 1z"/></svg>
    555-318-4762</p>

  <div class="abs bottom-band"></div>
  <div class="abs url-pill">www.<b>brevinhomeworks</b>.com</div>
</section>

</body>
</html>
```